Design 4 pages for an event discovery website

This is a contest for the design of 4 pages for an events discovery website. The feature is part of the new sign-up process.

Please see the attached document for a full scope, mockups and the parent category icons.

Target Market(s)

18-35 Australian event goers

Industry/Entity Type

Events

Number of Pages Required

4 page

```html
<!DOCTYPE html>
<html lang="en">
<head>
<meta charset="utf-8">
<title>Gigsora – Signup</title>
<link rel="stylesheet" href="https://fonts.googleapis.com/css2?family=Open+Sans:wght@400;600;700&display=swap">
<style>
  :root {
    --brand: #67c4d5;
    --white: #ffffff;
    --placeholder: #6f6f6f;
    --stage-top: #0c1218;
    --stage-mid: #1d3442;
    --stage-low: #3d6478;
    --footer: #1d1d1d;
    --footer-text: #a8a8a8;
    --button-dark: #2b2b2b;
    --button-light: #4a4a4a;
    --icon: #5a6670;
  }
  * { box-sizing: border-box; margin: 0; padding: 0; }
  html, body {
    width: 1200px; height: 788px; overflow: hidden;
    font-family: "Open Sans", Arial, sans-serif;
  }
  .page { position: relative; width: 1200px; height: 788px; overflow: hidden; background: var(--stage-top); }

  /* Header */
  .site-header { position: absolute; left: 0; top: 0; width: 1200px; height: 82px; background: var(--brand); }
  .brand { position: absolute; left: 119px; top: 14px; display: flex; align-items: baseline; color: var(--white); }
  .brand-name { font-size: 44px; font-weight: 600; letter-spacing: -1px; }
  .brand-tagline { font-size: 15px; font-weight: 600; margin-left: 10px; }
  .search {
    position: absolute; left: 696px; top: 21px; width: 209px; height: 40px;
    background: var(--white); border-radius: 3px; display: flex; align-items: center;
    padding: 0 12px 0 15px; font-size: 13px; color: #9a9a9a;
  }
  .search span { flex: 1; }
  .nav-button {
    position: absolute; top: 21px; height: 40px; border-radius: 3px;
    background: linear-gradient(#ffffff 0%, #f2f2f2 60%, #dcdcdc 100%);
    color: #777; font-size: 16px; display: flex; align-items: center; justify-content: center;
    box-shadow: 0 1px 2px rgba(0,0,0,.2);
  }
  .nav-signup { left: 912px; width: 81px; }
  .nav-login { left: 1000px; width: 81px; }

  /* Hero */
  .hero-backdrop {
    position: absolute; left: 0; top: 82px; width: 1200px; height: 624px;
    background:
      radial-gradient(ellipse 300px 140px at 250px 560px, rgba(170,210,230,.35), transparent),
      radial-gradient(ellipse 320px 140px at 900px 560px, rgba(170,210,230,.3), transparent),
      linear-gradient(180deg, var(--stage-top) 0%, #101b24 35%, var(--stage-mid) 65%, var(--stage-low) 88%, #16222b 100%);
  }
  .page-title {
    position: absolute; left: 120px; top: 160px; font-size: 42px; font-weight: 600; color: var(--white);
  }
  .signup-panel { position: absolute; left: 121px; top: 230px; width: 459px; height: 307px; background: var(--brand); }
  .field {
    position: absolute; width: 208px; height: 40px; background: var(--white); border-radius: 3px;
    font-size: 14px; color: var(--placeholder); padding-left: 15px; display: flex; align-items: center;
  }
  .field-error { position: absolute; font-size: 10px; line-height: 12px; color: var(--white); text-align: right; width: 204px; }
  .col-a { left: 16px; }
  .col-b { left: 238px; }
  .calendar { position: absolute; right: 8px; top: 8px; }
  .signup-button {
    position: absolute; left: 16px; top: 240px; width: 137px; height: 50px; border-radius: 3px;
    background: linear-gradient(var(--button-light), var(--button-dark));
    color: var(--white); font-size: 22px; font-weight: 700; display: flex; align-items: center; justify-content: center;
  }

  .benefits { position: absolute; left: 607px; top: 229px; width: 540px; list-style: none; color: var(--white); }
  .benefits li {
    position: relative; font-size: 16.5px; font-weight: 600; line-height: 20.5px; padding-left: 15px;
    margin-bottom: 20.5px; white-space: nowrap; text-shadow: 0 1px 3px rgba(0,0,0,.8);
  }
  .benefits li::before { content: "•"; position: absolute; left: 0; top: 0; }

  /* Footer */
  .site-footer { position: absolute; left: 0; top: 706px; width: 1200px; height: 82px; background: var(--footer); }
  .copyright { position: absolute; left: 119px; top: 30px; font-size: 13.5px; color: var(--footer-text); }
  .social { position: absolute; left: 761px; top: 24px; display: flex; gap: 8px; }
  .social span { width: 33px; height: 33px; border-radius: 50%; background: var(--icon); }
</style>
</head>
<body>
<div class="page">
  <header class="site-header">
    <div class="brand"><span class="brand-name">Gigsora</span><span class="brand-tagline">Find Events</span></div>
    <div class="search"><span>Search</span>
      <svg width="18" height="18" viewBox="0 0 18 18" aria-hidden="true"><circle cx="7.5" cy="7.5" r="5.5" fill="none" stroke="#9a9a9a" stroke-width="2.4"/><line x1="11.5" y1="11.5" x2="16" y2="16" stroke="#9a9a9a" stroke-width="2.8" stroke-linecap="round"/></svg>
    </div>
    <div class="nav-button nav-signup">Signup</div>
    <div class="nav-button nav-login">Login</div>
  </header>

  <div class="hero-backdrop" role="img" aria-label="Photo of a concert stage lit by bright spotlights"></div>

  <h1 class="page-title">Signup</h1>

  <form class="signup-panel">
    <div class="field col-a" style="top:18px">Username</div>
    <div class="field col-b" style="top:18px">E-mail Address</div>
    <div class="field-error col-a" style="top:61px">Error message</div>
    <div class="field-error col-b" style="top:61px">Error message</div>
    <div class="field col-a" style="top:82px">Password</div>
    <div class="field col-b" style="top:82px">Confirm Password</div>
    <div class="field col-a" style="top:134px">First name</div>
    <div class="field col-b" style="top:134px">Last name</div>
    <div class="field col-a" style="top:186px">Date of Birth
      <svg class="calendar" width="26" height="25" viewBox="0 0 26 25" aria-hidden="true">
        <rect x="0" y="2" width="26" height="23" rx="1" fill="#b5b5b5"/>
        <rect x="2" y="7" width="22" height="16" fill="#ffffff"/>
        <g fill="#b5b5b5">
          <rect x="3" y="8" width="4" height="3"/><rect x="8" y="8" width="4" height="3"/><rect x="13" y="8" width="4" height="3"/><rect x="18" y="8" width="4" height="3"/>
          <rect x="3" y="12" width="4" height="3"/><rect x="8" y="12" width="4" height="3"/><rect x="13" y="12" width="4" height="3"/><rect x="18" y="12" width="4" height="3"/>
          <rect x="3" y="16" width="4" height="3"/><rect x="8" y="16" width="4" height="3"/><rect x="13" y="16" width="4" height="3"/><rect x="18" y="16" width="4" height="3"/>
        </g>
      </svg>
    </div>
    <div class="signup-button">SIGNUP</div>
  </form>

  <ul class="benefits">
    <li>Get personalised event recommendations</li>
    <li>Get notified about your favourite events -<br>never miss out again</li>
    <li>Follow all your favourite artists, musicians, teams and<br>players in one place</li>
    <li>Follow your favourite local venues to know everything<br>happening there</li>
    <li>Get curated news and feature content on your favourite<br>artists (coming soon)</li>
    <li>Invite your mates to events via Crewvine (CV sign-up only)</li>
  </ul>

  <footer class="site-footer">
    <p class="copyright">Copyright &copy; 2015 Gigsora. All rights reserved</p>
    <div class="social" aria-label="Social links">
      <span></span><span></span><span></span><span></span><span></span><span></span><span></span><span></span>
    </div>
  </footer>
</div>
</body>
</html>
```